Brochure Brightwell Hearth Partners

Brochure 12 x 9 tri fold with insert/ Rack card 9x4. Brightwell Hearth Partners 318 Corvane Street Harlow Bay, NE 21629410-822-2207AgingAtHomeSolution.com Tag: Devoted to Thoughtful Household Support.
What we do: Home care agency that services higher end Clients Artsy area on the water. Taking care of seniors in their home.

Our story: Opening Brightwell Hearth Partners, Inc. is my way of making a difference in an industry that is dominated by franchises that often have their policies dictated by corporate policy-makers who are unfamiliar with local customs. My goal is to raise the level of non-medical home health care in our area by providing additional, customized training, higher wages for our care-partners and an inclusive workforce in the decision-making process when developing customized care planning for our clients. Through collaboration with the client, their family and care-partners I have learned what issues, concerns and disappointments may arise which enables me to provide a more defined solution for those in need.My goal of providing superior training required locating a nationally recognized curriculum that would serve our clients’ needs. I found the perfect fit with Norla Vance’s, Kindred Pathway Method™ and her Shifting Stones Series™. These programs provide our care-partners with the tools needed to handle the challenges of natural aging and living with Dementia. I was so impressed with these programs, I became a Certified Independent Trainer; one of five in the State of Maryland. There is a bonus for our care-partners who are required to maintain Continuing Education Units - these programs qualify for credit! Improving our industry by providing exemplary care-partners is my goal!I look forward to assisting you with your needs! Dana Prewitt Owner

Services: Companion Care Service - Conversation and Companionship , Meal Preparation, Light House Keeping, Errand Service ,Grocery Shopping ,Incidental Transportation, Laundry & Linen Washing, Medication Reminders, Recreational Activities ,
Personal Care Services: Bathing ,Mobility ,Transferring & Positioning ,Incontinence Care ,Oral Hygiene ,Feeding, Toileting ,Grooming & Dressing, Special Diet Preparation.

Our Commitment to You: Extensive Care-Partner Education - We provide, in addition to state mandated training, eight additional hours of hands-on Dementia training from a Certified, Independent Instructor on the “Kindred Pathway Method” by Norla Vance, a nationally recognized instructor on aging.

Nutrition/Local Chef Inspired Training ;We provide six, two-hour food preparation sessions for our care-partners using local chefs, their recipes and locally grown food.

Meaningful & Engaging Activities - We provide a monthly list with local activities to our care-partners based on our client’s interest and capabilities. Focusing on what our client loved to do in the past.

Home Solutions When Needed; We provide management services to help keep our clients in their homes by working with current contractors or locating new ones to properly maintain a safe-living environment.

About owner: Dana Prewitt, owner of Brightwell Hearth Partners, has earned her certification as an Independent Trainer in the Kindred Pathway; Method (KPM) by Norla Vance, a nationally recognized instructor on natural aging and aging with Dementia. Dana is one of five certified independent trainers in the state of Maryland. All staff will have eight hours of hands on Dementia Kindred Pathway Method training.

On the insert 11x 4.25 want the top to be sticking out of the tri -fold "Dementia Experts . I would like to have shades of each STONE as it progresses
The Shifting STONES(R): The STONES model recognizes the dynamic nature of the human brain and its abilities. Unlike other cognitive models, it acknowledges that everyone’s abilities can change in a moment. Modifying environments, situations, interactions, and expectations will create either supportive positive opportunities or result in distress and a sense of failure. Just as gemstones need different settings and care to show their best characteristics, so do people. Rather than focusing on a person’s loss when there is brain change, seeing individuals as precious, unique, and capable encourages a care partnership and is the core of this model. Providing supportive settings for everyone, including care providers, allows them to use what they have to be their best. The STONES® advocate that everyone living with brain change when given the opportunity will shine. Norla Vance and Kindred Pathway Method

Sapphire ~ True Blue ~ Optimal Cognition, Healthy Brain•
True to self: personal preferences remain basically the same
• Can be flexible in thinking and appreciate multiple perspectives
• Stress/pain/fatigue may trigger Diamond state: back to Sapphire with relief
• Able to suppress and filter personal reactions: chooses effective responses
• Selects from options and can make informed decisions
• Processes well and able to successfully transition
• Aging doesn’t change ability: processing slows, more effort/time/practice needed
My brain is healthy - true blue. If I am aging normally or distressed, it may be hard for me to find words. I can describe what I am thinking so you understand. I may talk to myself because I am giving myself cues and prompts. I can learn new things and change habits, but it takes time and effort. Honoring my choices and preferences, when possible, is important. I need more time to make decisions. Give me the details and let me think about it before you need an answer. I am able to remember plans and information but supports are helpful. I may like specific prompts such as notes, calendars, and reminder calls. Health changes in vision, hearing, balance, coordination, depression, anxiety, pain, or medication may impact my behavior, but my cognitive abilities remain the same.

Diamond ~ Clear and Sharp ~ Routines and Rituals Rule
• Displays many facets: behavior and perspective can shift dramatically
• Prefers the familiar and may resist change: challenged by transitions
• More rigid and self-focused; sees wants as needs, when stressed
• Personal likes/dislikes in relationships/space/belongings etc, become more intense
• Reacts to changes in environment; benefits from familiar; functional/forgiving
• Needs repetition and time to absorb new/different information or routines
• Trusted authority figures can help: reacts better when respect is mutual
My overall cognition is clear and sharp. When happy and supported, I am capable and shine in my abilities. When distressed, I can be cutting and rigid and may see help as a threat. I have trouble seeing other points of view and may become less aware of boundaries or more possessive about my relationships, personal space, and belongings. I have many facets so people see me differently depending on the situation. This can cause conflict among my family, friends, or care team as it’s hard to tell if I am choosing my behavior or truly have limits in my ability. I can socially engage and have good cover skills. People will vary in their awareness of what is happening to me. I want to keep habits and environments as they have always been, even if they are problematic for me or others. I am often focused on the past, personal values, or finances. I will need help to make changes in my life; it’s hard for me. I can be in a Diamond state for reasons other than dementia.

Emerald ~ Green and On the Go With a Purpose ~ Naturally Flawed
• Sees self as able and independent, with limited awareness of changes in ability
• Lives in moments of clarity mixed with periods of loss in logic/reason/perspective
• Understanding and use of language change: vague words and many repeats
• Cues and support help when getting to/from places and doing daily routines
• Awareness of time, place, and situation will not always match current reality
• Strong emotional reactions are triggered by fears, desires, or unmet needs
Needs to know what comes next: seeks guidance and assistance to fill the day
I am flawed; it is part of being a natural emerald. I tend to be focused on what I want or need in this moment and may not be aware of my own safety or changing abilities. I can chat socially, but I typically miss one out of every four words and cannot accurately follow the meaning of longer conversations. I won’t remember the details of our time together, but I will remember how your body language and tone of voice made me feel. I may hide or misplace things and believe someone has taken them. My brain will make up information to fill in the blanks, which makes you think I am lying. If you try to correct me or argue, I may become resentful or suspicious of you. I am not always rational, but I don’t want to be made to feel incompetent. My brain plays tricks on me, taking me to different times and places in my life. When I am struggling, I may tell you, “I want to go home.” To provide the help and assistance I need, you must go with my flow, use a positive, partnered approach, and modify my environment.

Amber ~ Caught in a Moment of Time ~ Caution Required
• Focused on sensation: seeks to satisfy desires and tries to avoid what is disliked
•Environment can drive actions and reactions without awareness of safety
• Visual abilities are limited: focus is on pieces or parts, not the whole picture
• What happens to or around an Amber, may cause strong and surprising reactions
• Enters others’ space and crosses boundaries attempting to meet own needs
• Has periods of intense activity: may be very curious or repetitive with objects or actions
• Care is refused or seen as threatening, due to differences in perspective and ability.
Like a particle trapped in an amber, I am caught in a moment of time. It may surprise you to see how I take in the world around me. I may not know you or see you as a whole person. I react to you based on how you look, sound, move, smell, and respond to me. I like to do simple tasks over and over and may need to repeatedly move and touch, smell, taste, take or tear items apart. While it may exhaust or frustrate you, it soothes me. I don’t recognize danger; you will have to safeguard my environment. I’m intolerant to discomfort because my mouth, hands, feet, and genitalia are highly sensitive due to changes in my nervous system. Therefore, activities like eating, taking medication, mouth care, bathing, dressing, and toileting may distress me. Please notice my reaction and stop if I am resisting. I can’t help myself and one or both of us may get hurt emotionally and/or physically. If this happens, wait a few minutes, connect with me, and try a different approach; possibly substituting one area of focus for another.

Ruby ~ Deep and Strong in Color ~ Others Stop Seeing What is Possible
• Makes use of rhythm: can usually sing, hum, pray, sway, rock, clap, and dance
• When moving can’t stop; when stopped can’t get moving: needs guidance and help
• Big, strong movements are possible, while skilled abilities are being lost
• Danger exists due to limited abilities combined with automatic actions or reactions
• Tends to miss subtle hints, but gets magnified facial expressions and voice rhythms
• Can mimic actions or motions, but will struggle to understand instructions/gestures
• Able to pick up and hold objects, and yet not know what to do with them
As the deep red of a ruby masks detail, my obvious losses make my remaining abilities harder to notice. Although my fine motor skills have become very limited, remember that I am able to move and do simple things with my hands. You will need to anticipate, identify, and respond to all of my needs, even though I may not be aware of them. Plan to create a supportive environment, help with the details of care, and structure my day. Just as a crossing guard directs traffic, you will need to guide my movements and transitions. I can rarely stop or start on my own and switching gears is a challenge. Move with me first, then use your body to show me what you want me to do next, going one step at a time. Palm-beneath-Palm™ assistance helps me to feel safe and secure and to know what to do. Danger is part of my life, due to losses in visual skills, chewing abilities, balance, and coordination. You can reduce the risks to me, but not eliminate them. I can still have moments of joy when you are able to provide what gives me pleasure.

Pearl ~ Hidden Within a Shell ~ Beautiful Moments to Behold
• Will frequently recognize familiar touches, voices, faces, aromas, and tastes• Personhood survives, although all other capabilities are minimal
• Understanding input takes time: go slow and simplify for success
• In care, first get connected by offering comfort then use careful and caring touch
• Changes in the body are profound: weight loss, immobility, systems are failing
• As protective reflexes are lost, breathing, swallowing, and moving will be difficult
Care partners benefit from learning the art of letting go rather than simply giving up
While hidden like a pearl in an oyster shell, I will still have moments when I become alert and responsive. I am near the end of my life. Moments of connection create a sense of wholeness and value between us. Use our time together not just to provide care, but to comfort and connect with me. To help me complete life well, it’s important to honor my personhood when making medical or care decisions; please don’t talk about me as though I am not still here. I respond best to familiar voices and gentle rhythmic movements. I am ruled by reflexes and will startle easily. My brain is losing its ability to control and heal my body. Be prepared to see me having difficulty breathing or swallowing. My body may no longer desire food and drink as I prepare to leave this life. I may not be able to stop living without permission from you. Your greatest gift at this time in my life is to let me know that it is okay to go.

Target Market(s)

Children of seniors, seniors , rehabilitation centers

Requirements
Must have
• Nice photos of Seniors that are happy doing thing they like to do with help (Caregivers)
• Upbeat . Positive
Nice to have
• Processional looking - but very personal, we are taking care of their love ones
Should not have
• Not to feel like a cold hospital or end of life

```html
<!DOCTYPE html>
<html lang="en">
<head>
<meta charset="utf-8">
<title>Brightwell Hearth Partners – Rack Card and Tri-fold</title>
<link href="https://fonts.googleapis.com/css2?family=Lobster&family=Lora:wght@400;500&display=swap" rel="stylesheet">
<style>
  :root {
    --navy: #2b2a6e;
    --blue: #1479c2;
    --teal: #1f7fae;
    --paper: #ffffff;
    --ink: #2a2a2a;
    --stage: #e4e4e6;
    --photo-a: #e9d9c8;
    --photo-b: #a9bfdc;
  }
  * { box-sizing: border-box; margin: 0; padding: 0; }
  html, body { width: 761px; height: 1200px; overflow: hidden; }
  body { background: var(--stage); position: relative; font-family: "Lora", Georgia, serif; color: var(--ink); }

  .panel { position: absolute; background: var(--paper); overflow: hidden; box-shadow: 0 2px 8px rgba(0,0,0,.12); }

  /* shared front-panel content */
  .top-tab { position: absolute; top: 0; left: 0; width: 84%; height: 14px; background: var(--navy); border-bottom-right-radius: 10px; }
  .brand-name { position: absolute; left: 0; right: 0; top: 44px; text-align: center; font-family: "Lora", Georgia, serif; font-weight: 400; color: var(--teal); font-size: 27px; line-height: 1.08; }
  .tagline { position: absolute; left: 0; right: 0; top: 150px; text-align: center; font-family: "Lobster", cursive; font-size: 19px; line-height: 1.15; }
  .tagline .line-one { color: var(--navy); display: block; }
  .tagline .line-two { color: var(--blue); display: block; }
  .photo { position: absolute; left: 16px; right: 0; top: 210px; height: 160px; background: linear-gradient(135deg, var(--photo-a), #d8d4d0 55%, var(--photo-b)); border-top-left-radius: 14px; }
  .blurb { position: absolute; left: 4px; right: 4px; top: 386px; text-align: center; font-size: 9px; line-height: 1.5; white-space: nowrap; }
  .phone-line { position: absolute; left: 0; right: 0; top: 426px; text-align: center; font-size: 26px; color: var(--blue); letter-spacing: .5px; white-space: nowrap; }
  .phone-line svg { width: 16px; height: 20px; vertical-align: -2px; margin-right: 4px; fill: var(--navy); }
  .url-box { position: absolute; right: 0; bottom: 12px; width: 86%; height: 56px; background: var(--navy); border-top-left-radius: 14px; border-bottom-left-radius: 14px; color: #fff; font-size: 11.5px; display: flex; align-items: center; justify-content: center; white-space: nowrap; }

  /* rack card */
  .rack-card { left: 256px; top: 24px; width: 249px; height: 560px; }

  /* tri-fold */
  .trifold { position: absolute; left: 20px; top: 618px; width: 720px; height: 560px; box-shadow: 0 2px 8px rgba(0,0,0,.12); }
  .trifold .fold { position: absolute; top: 0; width: 240px; height: 560px; overflow: hidden; }
  .fold-about { left: 0; background: var(--paper); }
  .fold-contact { left: 240px; background: var(--blue); }
  .fold-cover { left: 480px; background: var(--paper); }
  .top-band { position: absolute; top: 0; left: 70px; width: 630px; height: 13px; background: var(--navy); border-radius: 0 0 10px 10px; z-index: 2; }

  .about-heading { position: absolute; left: 26px; top: 74px; font-family: "Lobster", cursive; font-size: 21px; color: var(--navy); }
  .about-heading .accent { color: var(--blue); }
  .about-text { position: absolute; left: 26px; right: 22px; top: 108px; font-size: 10.4px; line-height: 1.5; text-align: center; }
  .cert-badge { position: absolute; left: 62px; top: 352px; width: 112px; height: 112px; border-radius: 50%; background: radial-gradient(circle, #f4f6f2 0 56%, #c9cbd6 57% 62%, var(--navy) 63% 100%); }

  .contact-brand { position: absolute; left: 0; right: 0; top: 60px; text-align: center; font-family: "Lora", Georgia, serif; font-weight: 400; color: #fff; font-size: 26px; line-height: 1.08; }
  .contact-heading { position: absolute; left: 0; right: 0; top: 258px; text-align: center; font-family: "Lobster", cursive; font-size: 22px; color: #fff; }
  .contact-address { position: absolute; left: 46px; top: 302px; color: #fff; font-size: 11px; line-height: 1.4; padding-left: 18px; white-space: nowrap; }
  .contact-address svg { position: absolute; left: 0; top: 1px; width: 12px; height: 16px; fill: var(--navy); }
  .contact-phone { position: absolute; left: 0; right: 0; top: 344px; text-align: center; font-size: 22px; color: #fff; white-space: nowrap; }
  .contact-phone svg { width: 13px; height: 17px; vertical-align: -2px; margin-right: 4px; fill: var(--navy); }
  .contact-url { position: absolute; left: 24px; right: 24px; bottom: 24px; height: 58px; background: #fff; border-radius: 14px; color: var(--blue); font-size: 10.5px; display: flex; align-items: center; justify-content: center; white-space: nowrap; }

  .fold-cover .blurb { font-size: 9.2px; }
  .fold-cover .url-box { font-size: 11px; }
</style>
</head>
<body>

  <!-- Rack card front -->
  <section class="panel rack-card" aria-label="Rack card front">
    <div class="top-tab"></div>
    <h1 class="brand-name">Brightwell<br>Hearth<br>Partners</h1>
    <p class="tagline"><span class="line-one">Devoted to Thoughtful</span><span class="line-two">Household Support</span></p>
    <div class="photo" role="img" aria-label="Photo of a smiling senior woman with a caregiver holding a clipboard in a bright living room"></div>
    <p class="blurb">Home care agency that services higher end Clients.<br>Taking care of seniors in their home.</p>
    <p class="phone-line"><svg viewBox="0 0 16 20" aria-hidden="true"><path d="M4 1c1 0 2 3 2 4s-2 1.5-2 2.5 2 5 3.5 6 2-1 3-1 3.5 1.5 3.5 2.5-2 3-3.5 3C5 18 1 10 1 4.5 1 3 3 1 4 1z"/></svg>410-555-0148</p>
    <div class="url-box">BrightwellHearthPartners.example</div>
  </section>

  <!-- Tri-fold outside spread -->
  <section class="trifold" aria-label="Tri-fold brochure outside">
    <div class="top-band"></div>

    <div class="fold fold-about">
      <h2 class="about-heading"><span class="accent">About</span> owner</h2>
      <p class="about-text">Dana Prewitt, owner of Brightwell Hearth Partners, has earned her certification as an Independent Trainer in the Kindred Pathway Method (KPM) by Norla Vance, a nationally recognized instructor on natural aging and aging with Dementia. Dana is one of five certified independent trainers in the state of Maryland. All staff will have eight hours of hands on Dementia Kindred Pathway Method training.</p>
      <div class="cert-badge" role="img" aria-label="Certified independent trainer badge"></div>
    </div>

    <div class="fold fold-contact">
      <h2 class="contact-brand">Brightwell<br>Hearth<br>Partners</h2>
      <h3 class="contact-heading">Contact Us</h3>
      <p class="contact-address"><svg viewBox="0 0 12 16" aria-hidden="true"><path d="M6 0a6 6 0 0 1 6 6c0 4-6 10-6 10S0 10 0 6a6 6 0 0 1 6-6zm0 3.5a2.5 2.5 0 1 0 0 5 2.5 2.5 0 0 0 0-5z"/></svg>318 Corvane Street<br>Harlow Bay, NE 21774</p>
      <p class="contact-phone"><svg viewBox="0 0 16 20" aria-hidden="true"><path d="M4 1c1 0 2 3 2 4s-2 1.5-2 2.5 2 5 3.5 6 2-1 3-1 3.5 1.5 3.5 2.5-2 3-3.5 3C5 18 1 10 1 4.5 1 3 3 1 4 1z"/></svg>410-555-0148</p>
      <div class="contact-url">BrightwellHearthPartners.example</div>
    </div>

    <div class="fold fold-cover">
      <h1 class="brand-name">Brightwell<br>Hearth<br>Partners</h1>
      <p class="tagline"><span class="line-one">Devoted to Thoughtful</span><span class="line-two">Household Support</span></p>
      <div class="photo" role="img" aria-label="Photo of a smiling senior woman with a caregiver holding a clipboard in a bright living room"></div>
      <p class="blurb">Home care agency that services higher end Clients.<br>Taking care of seniors in their home.</p>
      <p class="phone-line"><svg viewBox="0 0 16 20" aria-hidden="true"><path d="M4 1c1 0 2 3 2 4s-2 1.5-2 2.5 2 5 3.5 6 2-1 3-1 3.5 1.5 3.5 2.5-2 3-3.5 3C5 18 1 10 1 4.5 1 3 3 1 4 1z"/></svg>410-555-0148</p>
      <div class="url-box">BrightwellHearthPartners.example</div>
    </div>
  </section>

</body>
</html>
```